yourCartly - a stylish trolley for apartments

We neede a simple website to sell our Trolley, for apartment use.
The colour theme is red, blask & white. Our logo is attached and this needs to be on the Home page.
The website only needs a Home Page plus 4 other pges.
In the attachment you will find a site map.

You can check out the following two sites to see what I like:
www.plainvexo.com/design-showcase-inspiration/minimalist-portfolio-website/
www.brightquillor.com/inspiration/40-beautiful-web-design-portfolios/ in this site especially
Dario Penhaske
G K Maker
Nine 17 Works
Marcus Bell

And especially Lamp - I ike the simpicity of the site esp as we are only selling one product

Target Market(s)

Apartment dwellers

Industry/Entity Type

Apartment

Requirements
Must have
• This website must have 4 pages.
We need Zorva, Pelicoin and Quidnet portals.
Order Form for Trolley
Payment form.

```html
<!DOCTYPE html>
<html lang="en">
<head>
<meta charset="utf-8">
<title>yourCartly – Home</title>
<link rel="stylesheet" href="https://fonts.googleapis.com/css2?family=PT+Sans:wght@400;700&family=Crimson+Text:wght@400&family=Arimo:wght@400&display=swap">
<style>
  :root{
    --black:#000;
    --red:#b40c0c;
    --red-line:#c2141b;
    --yellow:#f5b400;
    --page:#ebebeb;
    --white:#fff;
    --ink:#222;
    --ink-soft:#333;
    --muted:#555;
    --rule:#ddd;
  }
  *{box-sizing:border-box;margin:0;padding:0}
  html,body{width:955px;height:1200px;overflow:hidden}
  body{position:relative;background:var(--page);font-family:"PT Sans",sans-serif;color:var(--ink)}

  .site-header{position:absolute;left:0;top:0;width:955px;height:164px;background:var(--black);border-bottom:2px solid var(--red-line)}
  .brand{position:absolute;left:22px;top:56px;display:flex;align-items:center;gap:10px;color:var(--white);font-family:"PT Sans",sans-serif;font-weight:700;font-size:30px;letter-spacing:.3px}
  .brand-mark{width:22px;height:22px;background:var(--red)}

  .welcome-tab{position:absolute;left:550px;top:0;width:99px;height:27px;background:var(--yellow);border-radius:0 0 3px 3px;font-size:11px;font-weight:700;color:#111;text-align:center;line-height:29px}
  .account-links{position:absolute;left:659px;top:8px;font-size:11px;color:var(--white);display:flex;gap:7px}
  .account-links span.sep{color:#bbb}
  .cart{position:absolute;left:850px;top:4px;display:flex;align-items:center;gap:10px;font-size:11px;color:var(--white)}
  .cart-icon{width:22px;height:22px;border-radius:50%;background:var(--yellow);display:flex;align-items:center;justify-content:center}

  .search{position:absolute;left:649px;top:55px;width:276px;height:24px;display:flex}
  .search-field{flex:1;background:var(--white);border-radius:12px 0 0 12px;font-size:11px;font-style:italic;color:#888;padding:6px 0 0 12px}
  .search-btn{width:63px;background:var(--yellow);font-size:11px;color:#111;text-align:center;line-height:25px}

  .main-nav{position:absolute;left:488px;top:99px;display:flex;align-items:center;font-family:"Crimson Text",serif;font-size:15px;color:var(--white)}
  .main-nav .active{background:var(--red);border-radius:3px;width:98px;height:36px;line-height:36px;text-align:center}
  .main-nav .item{margin-left:21px}
  .main-nav .sep{margin-left:17px;color:#ccc}

  .content{position:absolute;left:23px;top:165px;width:908px;height:940px;background:var(--white);box-shadow:0 1px 4px rgba(0,0,0,.35)}

  .slider-frame{position:absolute;left:23px;top:14px;width:854px;height:353px;background:var(--white);border:1px solid #eee;box-shadow:0 6px 10px -4px rgba(0,0,0,.2)}
  .slide{position:absolute;left:16px;top:16px;width:825px;height:318px;background:linear-gradient(115deg,#3d3b33 0%,#6e6a5c 35%,#c9c8c0 60%,#5b5a52 80%,#2c2c28 100%)}
  .slider-arrow{position:absolute;top:313px;width:36px;height:36px;border-radius:50%;background:#333;border:2px solid #eee}
  .slider-arrow.prev{left:6px}
  .slider-arrow.next{left:866px}
  .slider-arrow svg{position:absolute;left:11px;top:11px}
  .dots{position:absolute;left:459px;top:381px;display:flex;gap:5px}
  .dot{width:9px;height:9px;border-radius:50%;background:#888}
  .dot.on{background:var(--red)}

  .intro-title{position:absolute;left:43px;top:422px;font-size:17px;font-weight:400;color:var(--ink)}
  .intro-title .accent{color:var(--red)}
  .intro{position:absolute;left:43px;top:454px;width:840px;font-size:12.3px;line-height:20px;color:var(--ink-soft)}
  .intro p{margin-bottom:20px}

  .products-title{position:absolute;left:40px;top:680px;font-size:17px;font-weight:400}
  .product{position:absolute;top:712px;width:240px}
  .product-photo{width:240px;height:115px;border:1px solid var(--rule);padding:3px;background:var(--white);box-shadow:0 1px 2px rgba(0,0,0,.1)}
  .product-photo div{width:100%;height:100%}
  .p1 .product-photo div{background:linear-gradient(90deg,#4a463c,#8f8c80 55%,#c6c4bb)}
  .p2 .product-photo div{background:linear-gradient(90deg,#7c7b76,#b4b3ae 50%,#6f6e6a)}
  .p3 .product-photo div{background:linear-gradient(90deg,#cfcdc6,#6a6659 45%,#3a3832)}
  .product-text{margin:10px 0 0 7px;font-family:"Arimo",Arial,sans-serif;font-size:10.5px;line-height:17px;color:var(--ink-soft);width:225px}
  .details-btn{position:absolute;left:10px;top:206px;width:76px;height:27px;background:var(--black);color:var(--white);border-radius:4px;font-family:"Arimo",Arial,sans-serif;font-size:12px;text-align:center;line-height:27px}

  .social{position:absolute;left:33px;top:1138px;display:flex;gap:4px}
  .social span{width:27px;height:27px;border-radius:4px;display:block}
  .social .s1{background:#2d4f94}
  .social .s2{background:#2aa3d4}
  .social .s3{background:#1a6fb3}
  .social .s4{background:#e8751c}
  .footer-links{position:absolute;right:29px;top:1138px;font-family:"Arimo",Arial,sans-serif;font-size:12px;color:var(--muted);display:flex;gap:16px}
  .copyright{position:absolute;right:24px;top:1170px;font-family:"Arimo",Arial,sans-serif;font-size:12px;color:#333}
</style>
</head>
<body>
  <header class="site-header">
    <div class="brand"><span class="brand-mark"></span>yourCartly</div>
    <div class="welcome-tab">Welcome, visitor</div>
    <nav class="account-links"><span>My Account</span><span class="sep">|</span><span>Register</span><span class="sep">|</span><span>Login</span></nav>
    <div class="cart">
      <span class="cart-icon"><svg width="12" height="10" viewBox="0 0 12 10"><path d="M0 1h2l1.5 6h6L11 3H3" fill="none" stroke="#6b4a00" stroke-width="1.3"/><circle cx="4.5" cy="9" r="1" fill="#6b4a00"/><circle cx="8.5" cy="9" r="1" fill="#6b4a00"/></svg></span>
      <span>(0) Items</span>
    </div>
    <form class="search"><div class="search-field">type your word here</div><div class="search-btn">SEARCH</div></form>
    <nav class="main-nav">
      <span class="active">yourCartly</span>
      <span class="item">Gallery</span><span class="sep">|</span>
      <span class="item">Shopping Cart Payment</span><span class="sep">|</span>
      <span class="item">Contact us</span>
    </nav>
  </header>

  <main class="content">
    <div class="slider-frame">
      <div class="slide" role="img" aria-label="Photo of a couple loading shopping and luggage from a white car onto the trolley in an underground car park"></div>
    </div>
    <span class="slider-arrow prev"><svg width="10" height="12" viewBox="0 0 10 12"><path d="M7 1L2 6l5 5" fill="none" stroke="#fff" stroke-width="2"/></svg></span>
    <span class="slider-arrow next"><svg width="10" height="12" viewBox="0 0 10 12"><path d="M3 1l5 5-5 5" fill="none" stroke="#fff" stroke-width="2"/></svg></span>
    <div class="dots"><span class="dot"></span><span class="dot"></span><span class="dot on"></span><span class="dot"></span><span class="dot"></span></div>

    <h1 class="intro-title">WELCOME TO <span class="accent">your</span>Cartly</h1>
    <div class="intro">
      <p>yourCartly evolved from demand! &nbsp;Apartment dwellers everywhere are calling for a solution to moving shopping, luggage and other goods from car to apartment, and vice versa. Other trolleys on the market are not versatile, they are not robust, but more importantly, they are NOT stylish! The emphasis of yourCartly is on style. This trolley is stylish enough to remain in your apartment as a piece of furniture. It features a versatile flat-bed and hanger, to cope with all your transport needs.</p>
      <p>IT LOOKS GREAT! &nbsp;Designed along the lines of the familiar hotel “birdcage” luggage trolley, it provides smart and practical use for all small transport needs.<br>The stylish trolley does not need to be disassembled and stored away in a cupboard or storage area. It can live in the apartment, proudly! &nbsp;Trolleys with plastic coated wire baskets soon become shabby and chipped.</p>
      <p>yourCartly is made of high quality stainless steel and other robust materials. Whilst other trolleys tend to look like they belong in a factory or workshop, yourCartly is the classy alternative, which can live anywhere in your apartment, and not in the cupboard. So – we welcome yourCartly &nbsp;to the marketplace!</p>
    </div>

    <h2 class="products-title">Our Products</h2>
    <article class="product p1" style="left:38px">
      <div class="product-photo"><div role="img" aria-label="Photo of the trolley loaded with bags beside an open car boot"></div></div>
      <p class="product-text">Nunc varius facilisis eros. Sed erat. In in velit quis arcu ornare laoreet. Curabitur adipiscing luctus massa.Integer ut ac augue commodo .</p>
      <span class="details-btn">Details</span>
    </article>
    <article class="product p2" style="left:325px">
      <div class="product-photo"><div role="img" aria-label="Photo of the trolley with luggage waiting by a lift"></div></div>
      <p class="product-text">Nunc varius facilisis eros. Sed erat. In in velit quis arcu ornare laoreet. Curabitur adipiscing luctus massa.Integer ut ac augue commodo .</p>
      <span class="details-btn">Details</span>
    </article>
    <article class="product p3" style="left:613px">
      <div class="product-photo"><div role="img" aria-label="Photo of a man hanging garments on the trolley next to a car"></div></div>
      <p class="product-text">Nunc varius facilisis eros. Sed erat. In in velit quis arcu ornare laoreet. Curabitur adipiscing luctus massa.Integer ut ac augue commodo .</p>
      <span class="details-btn">Details</span>
    </article>
  </main>

  <footer>
    <div class="social"><span class="s1"></span><span class="s2"></span><span class="s3"></span><span class="s4"></span></div>
    <nav class="footer-links"><span>Privacy Policy</span><span>|</span><span>Terms &amp; Conditions</span><span>|</span><span>Contact Us</span></nav>
    <p class="copyright">© 2012 yourCartly, All Rights Reserved</p>
  </footer>
</body>
</html>
```